Local Roofing/Construction company business needs new biz card design

We need a new business card design, current cards are from the start of this operation and generic at best. We are a local Construction Company (General Contractor) with a majority of our work originating from insurance claims-exterior finish work is the main focus (Roofs-Siding-Gutters etc). Heavily involved with homeowners and the low ball offers they receive from insurance company's after a insurable event takes place. I have attached some of our original logo file(s) below.

```html
<!DOCTYPE html>
<html lang="en">
<head>
<meta charset="utf-8">
<title>Halden Ridge Construction – Business Card</title>
<link href="https://fonts.googleapis.com/css2?family=Open+Sans:wght@400;600;700&display=swap" rel="stylesheet">
<style>
  :root {
    --stage: #333333;
    --card: #061d22;
    --card-edge: #0b2a30;
    --accent: #4cbb6c;
    --ink: #ffffff;
    --ink-soft: #e9eeee;
    --mark: #7f8f92;
  }
  * { box-sizing: border-box; margin: 0; padding: 0; }
  html, body {
    width: 1200px; height: 780px; overflow: hidden;
    background: var(--stage);
    font-family: "Open Sans", Arial, sans-serif;
  }
  .stage {
    width: 1200px; height: 780px;
    display: flex; align-items: center; justify-content: center; gap: 40px;
  }
  .card {
    position: relative;
    width: 540px; height: 309px;
    background: var(--card);
    border: 1px solid var(--card-edge);
    box-shadow: 0 12px 30px rgba(0,0,0,.45);
    overflow: hidden;
  }

  /* Company name */
  .brand {
    display: flex; align-items: center; gap: 14px;
    color: var(--mark); font-weight: 700; letter-spacing: 2px;
    text-transform: uppercase;
  }
  .brand-square { width: 22px; height: 22px; background: var(--mark); flex: none; }
  .brand-line { display: block; white-space: nowrap; line-height: 1.05; }

  .card-back { display: flex; align-items: center; justify-content: center; }
  .card-back .brand-name { font-size: 30px; }

  .front-brand {
    position: absolute; left: 494px; top: 154px;
    transform: translate(-50%, -50%) rotate(-90deg);
    gap: 10px;
  }
  .front-brand .brand-name { font-size: 17px; }
  .front-brand .brand-square { width: 15px; height: 15px; }

  /* Contact side */
  .front-info { position: absolute; left: 0; top: 84px; }
  .name-block { position: relative; padding-left: 38px; }
  .name-block::before {
    content: ""; position: absolute; left: 18px; top: 4px;
    width: 9px; height: 58px; background: var(--accent);
  }
  .person-name { font-size: 27px; font-weight: 700; line-height: 1.1; color: var(--ink); }
  .person-name .first { color: var(--accent); }
  .person-title { font-size: 15px; font-weight: 600; color: var(--ink); margin-top: 4px; }
  .address {
    padding-left: 44px; margin-top: 12px;
    font-size: 13px; line-height: 1.35; color: var(--ink-soft);
  }
  .contacts { list-style: none; padding-left: 44px; margin-top: 10px; }
  .contacts li {
    display: flex; align-items: center; gap: 9px;
    font-size: 13px; line-height: 1.45; color: var(--ink-soft);
  }
  .contacts svg { width: 12px; height: 12px; fill: var(--accent); flex: none; }
</style>
</head>
<body>
<main class="stage">
  <section class="card card-back" aria-label="Card back">
    <div class="brand">
      <span class="brand-square"></span>
      <span class="brand-name"><span class="brand-line">Halden Ridge</span><span class="brand-line">Construction</span></span>
    </div>
  </section>

  <section class="card card-front" aria-label="Card front">
    <div class="front-info">
      <div class="name-block">
        <h1 class="person-name"><span class="first">Marta</span> Velkova</h1>
        <p class="person-title">Managing Director</p>
      </div>
      <p class="address">245 Oak Hollow<br>Dr, Fairbrook, MO 63410</p>
      <ul class="contacts">
        <li><svg viewBox="0 0 24 24"><path d="M6.6 10.8a15.1 15.1 0 0 0 6.6 6.6l2.2-2.2a1 1 0 0 1 1-.25 11.4 11.4 0 0 0 3.6.57 1 1 0 0 1 1 1V20a1 1 0 0 1-1 1A17 17 0 0 1 3 4a1 1 0 0 1 1-1h3.5a1 1 0 0 1 1 1c0 1.25.2 2.45.57 3.57a1 1 0 0 1-.25 1z"/></svg>555-210-4836</li>
        <li><svg viewBox="0 0 24 24"><path d="M6.6 10.8a15.1 15.1 0 0 0 6.6 6.6l2.2-2.2a1 1 0 0 1 1-.25 11.4 11.4 0 0 0 3.6.57 1 1 0 0 1 1 1V20a1 1 0 0 1-1 1A17 17 0 0 1 3 4a1 1 0 0 1 1-1h3.5a1 1 0 0 1 1 1c0 1.25.2 2.45.57 3.57a1 1 0 0 1-.25 1z"/></svg>555-210-7792 (Emergency)</li>
        <li><svg viewBox="0 0 24 24"><circle cx="12" cy="12" r="10"/></svg>www.haldenridgebuild.com</li>
        <li><svg viewBox="0 0 24 24"><path d="M2 5h20v14H2zm2 2v.5l8 5 8-5V7l-8 5z"/></svg>office@haldenridgebuild.com</li>
      </ul>
    </div>
    <div class="brand front-brand">
      <span class="brand-square"></span>
      <span class="brand-name"><span class="brand-line">Halden Ridge</span><span class="brand-line">Construction</span></span>
    </div>
  </section>
</main>
</body>
</html>
```